Property management company looking for modern card design

We at Blue Heron Partners provides property management services for its residential and commercial properties, with expertise in all categories of multifamily, industrial and office projects throughout California.

We need a business card design that is professional and modern designed business card. In our field, clients get hundreds of business cards, we would like our card to stand out.

Please avoid small print.

Target Market(s)

Professionals and high end clients

Industry/Entity Type

Financial Planning

Contact Information for Business Card

Company Name: Blue Heron Partners, Name, email, license #, phone number, website blueheronpartners.com

Font styles to use
Sans Serif

Requirements
Must have
• The card design needs to be adaptable because there is a possibly we will be expanding into different sectors other than real estate. The card design should be focused on financial planning and asset management.
Nice to have
• Modern and simple business card. Eye catching. Non-standard size/shaped cards would be great.
• blueheronpartners.com
Should not have
• Too many bright color or any pictures or shapes of real estate stuff.

```html
<!DOCTYPE html>
<html lang="en">
<head>
<meta charset="utf-8">
<title>Blue Heron Partners – Business Card</title>
<link rel="stylesheet" href="https://fonts.googleapis.com/css2?family=Lato:wght@400;700&display=swap">
<style>
  :root {
    --stage: #b8c2d3;
    --card-black: #0b0c0d;
    --card-sheen: #24272a;
    --brand-orange: #f2821f;
    --text-light: #f2f2f2;
    --text-dark: #1a1a1a;
    --rule: #5a5d60;
  }
  html, body {
    margin: 0;
    padding: 0;
    width: 1200px;
    height: 502px;
    overflow: hidden;
    background: var(--stage);
    font-family: "Lato", Arial, sans-serif;
  }
  p { margin: 0; }
  .canvas {
    position: relative;
    width: 1200px;
    height: 502px;
  }
  .card {
    position: absolute;
    top: 102px;
    height: 292px;
    overflow: hidden;
    background: var(--card-black);
  }
  .card-texture {
    position: absolute;
    inset: 0;
    background:
      radial-gradient(ellipse 70% 40% at 85% 5%, var(--card-sheen), transparent 70%),
      radial-gradient(ellipse 60% 80% at 100% 90%, #1c1e20, transparent 70%),
      var(--card-black);
  }
  /* Front */
  .card-front { left: 66px; width: 508px; }
  .front-brand {
    position: absolute;
    left: 0;
    right: 0;
    top: 124px;
    display: flex;
    justify-content: center;
    align-items: center;
    gap: 14px;
  }
  .front-square {
    width: 22px;
    height: 22px;
    background: var(--brand-orange);
  }
  .front-name {
    font-size: 34px;
    font-weight: 400;
    color: var(--text-light);
  }
  /* Back */
  .card-back { left: 630px; width: 512px; }
  .contact-list {
    position: absolute;
    left: 0;
    top: 0;
    width: 324px;
    height: 292px;
    margin: 0;
    padding: 0;
    list-style: none;
  }
  .contact-item {
    position: absolute;
    left: 18px;
    display: flex;
    align-items: center;
    gap: 16px;
    color: var(--text-light);
    font-size: 18px;
    letter-spacing: 0.3px;
  }
  .contact-item svg { width: 40px; height: 40px; flex: none; }
  .item-name { top: 16px; }
  .item-phone { top: 76px; }
  .item-email { top: 144px; }
  .item-web { top: 202px; }
  .license-rule {
    position: absolute;
    left: 0;
    width: 324px;
    top: 252px;
    border-top: 1px solid var(--rule);
  }
  .license {
    position: absolute;
    left: 0;
    width: 324px;
    top: 264px;
    text-align: center;
    font-size: 14px;
    line-height: 16px;
    color: var(--text-light);
    letter-spacing: 0.4px;
  }
  .brand-panel {
    position: absolute;
    left: 324px;
    top: 0;
    width: 188px;
    height: 292px;
    background: var(--brand-orange);
  }
  .panel-name {
    position: absolute;
    left: 0;
    right: 0;
    top: 118px;
    text-align: center;
    font-size: 24px;
    line-height: 30px;
    font-weight: 400;
    color: var(--text-dark);
  }
</style>
</head>
<body>
<main class="canvas">

  <section class="card card-front" aria-label="Card front">
    <div class="card-texture" role="img" aria-label="Dark background with fine flowing line texture"></div>
    <div class="front-brand">
      <span class="front-square"></span>
      <p class="front-name">Blue Heron Partners</p>
    </div>
  </section>

  <section class="card card-back" aria-label="Card back">
    <div class="card-texture" role="img" aria-label="Dark background with fine flowing line texture"></div>

    <ul class="contact-list">
      <li class="contact-item item-name">
        <svg viewBox="0 0 40 40" aria-hidden="true">
          <circle cx="20" cy="20" r="19" fill="#fff"/>
          <circle cx="20" cy="16" r="6" fill="#0b0c0d"/>
          <path d="M9 30c1.5-6 5.5-8 11-8s9.5 2 11 8z" fill="#0b0c0d"/>
        </svg>
        INDIVIDUAL NAME
      </li>
      <li class="contact-item item-phone">
        <svg viewBox="0 0 40 40" aria-hidden="true">
          <path d="M9 6l6 0 3 8-4 3c2 5 5 8 10 10l3-4 8 3v6c0 2-2 3-4 3C18 34 6 22 6 9c0-2 1-3 3-3z" fill="#fff"/>
        </svg>
        PHONE NUMBER
      </li>
      <li class="contact-item item-email">
        <svg viewBox="0 0 40 40" aria-hidden="true">
          <rect x="3" y="14" width="34" height="22" fill="none" stroke="#fff" stroke-width="1.6"/>
          <path d="M3 36l14-11M37 36L23 25M3 14l17 13 17-13" fill="none" stroke="#fff" stroke-width="1.6"/>
          <rect x="11" y="3" width="18" height="17" fill="#fff"/>
          <text x="20" y="15.5" text-anchor="middle" font-size="11" font-family="Arial, sans-serif" font-weight="700" fill="#0b0c0d">@</text>
        </svg>
        E-MAIL
      </li>
      <li class="contact-item item-web">
        <svg viewBox="0 0 40 40" aria-hidden="true" fill="none" stroke="#fff" stroke-width="1.5">
          <circle cx="20" cy="20" r="16"/>
          <ellipse cx="20" cy="20" rx="7" ry="16"/>
          <path d="M4 20h32M20 4v32M7 12h26M7 28h26"/>
        </svg>
        www.blueheronpartners.com
      </li>
    </ul>

    <div class="license-rule"></div>
    <p class="license">LICENSE NUMBER</p>

    <div class="brand-panel">
      <p class="panel-name">Blue Heron<br>Partners</p>
    </div>
  </section>

</main>
</body>
</html>
```